Electrician Letterhead Design MVR

We need some letterhead for our bills and other papers.
Customer address is on the right side (Swiss format)
A4 format

Design should also be applicable on Cards

Target Market(s)

Private Customers, Small Business

Industry/Entity Type

Electrician

Other font styles liked:
• incised 901

Colors
00AB8E
00BBA5
67D7C9
C6EFE9
E9F9F6

```html
<!DOCTYPE html>
<html lang="en">
<head>
<meta charset="utf-8">
<title>MVR Letterhead</title>
<link href="https://fonts.googleapis.com/css2?family=Lato:wght@400;700;900&family=Parisienne&display=swap" rel="stylesheet">
<style>
  :root {
    --teal-dark: #00A08A;
    --teal-light: #72C2B8;
    --ink: #2b2b2b;
    --ink-soft: #3c3c3c;
    --paper: #ffffff;
    --backdrop: #e4e4e4;
  }
  * { box-sizing: border-box; margin: 0; padding: 0; }
  html, body {
    width: 1200px; height: 874px; overflow: hidden;
    background: var(--backdrop);
    font-family: "Lato", sans-serif;
    color: var(--ink);
  }
  .letterhead {
    position: absolute; left: 310px; top: 27px;
    width: 580px; height: 820px;
    background: var(--paper);
    box-shadow: 0 6px 24px rgba(0,0,0,0.12);
    overflow: hidden;
  }
  .brand {
    position: absolute; left: 62px; top: 62px;
    display: flex; align-items: center; gap: 8px;
  }
  .brand-square { width: 14px; height: 14px; background: var(--teal-dark); }
  .brand-name {
    font-weight: 900; font-size: 44px; letter-spacing: 1px;
    color: var(--teal-dark); line-height: 1;
  }
  .contact {
    position: absolute; left: 420px; top: 40px;
    border-left: 1px solid var(--teal-dark);
    padding-left: 8px;
    font-style: normal;
    font-size: 7.5px; line-height: 11px; color: var(--ink);
  }
  .contact-row { display: flex; align-items: center; gap: 4px; }
  .contact-row svg { width: 6px; height: 6px; fill: var(--teal-dark); }
  .contact-gap { padding-left: 10px; }
  .recipient {
    position: absolute; left: 62px; top: 165px;
    font-size: 11px; line-height: 14px; color: var(--ink-soft);
  }
  .recipient p { margin-bottom: 10px; }
  .letter-body {
    position: absolute; left: 62px; top: 290px; width: 455px;
    font-size: 10.5px; line-height: 14px; color: var(--ink-soft);
  }
  .salutation { font-weight: 700; font-size: 13px; color: var(--ink); margin-bottom: 10px; }
  .letter-body p.para { margin-bottom: 14px; }
  .closing { margin-top: 18px; font-size: 11px; }
  .signature {
    font-family: "Parisienne", cursive;
    font-size: 34px; color: var(--ink); margin-top: 10px;
  }
  .footer-rule {
    position: absolute; left: 0; right: 0; bottom: 26px;
    height: 4px; background: var(--teal-light);
  }
  .footer-band {
    position: absolute; left: 0; right: 0; bottom: 0;
    height: 18px; background: var(--teal-dark);
  }
</style>
</head>
<body>
  <main class="letterhead">
    <div class="brand">
      <span class="brand-square"></span>
      <span class="brand-name">MVR</span>
    </div>

    <address class="contact">
      <div class="contact-gap">42 Linden Road 7,</div>
      <div class="contact-gap">Fairview, NY 10290</div>
      <div class="contact-row">
        <svg viewBox="0 0 10 10"><path d="M2 1h2l1 2-1.5 1a6 6 0 0 0 2.5 2.5L7 5l2 1v2a1 1 0 0 1-1 1A8 8 0 0 1 1 2a1 1 0 0 1 1-1z"/></svg>
        555-017-2834
      </div>
      <div class="contact-row">
        <svg viewBox="0 0 10 10"><path d="M0 2h10v6H0z"/></svg>
        hello@mvr-mail.com
      </div>
      <div class="contact-row">
        <svg viewBox="0 0 10 10"><circle cx="5" cy="5" r="5"/></svg>
        www.mvr-electric.com
      </div>
    </address>

    <section class="recipient">
      <p>Feb-03-2022</p>
      <p>Mr. Peter Lang<br>President</p>
      <p>Nordline Corporation<br>123 Street Name, Suite# 10<br>City, State, 120023</p>
    </section>

    <article class="letter-body">
      <p class="salutation">Dear Mr. Lang</p>
      <p class="para">Lorem ipsum dolor sit amet, consectetur adipisicing elit, sed do eiusmod tempor incididunt ut labore et dolore magna aliqua. Ut enim ad minim veniam, quis nostrud exercitation ullamco laboris nisi ut aliquip ex ea commodo consequat. Duis aute irure dolor in reprehenderit in voluptate velit esse cillum dolore eu fugiat nulla pariatur.</p>
      <p class="para">Lorem ipsum dolor sit amet, consectetur adipisicing elit, sed do eiusmod tempor incididunt ut labore et dolore magna aliqua. Ut enim ad minim veniam, quis nostrud exercitation ullamco laboris nisi ut aliquip ex ea commodo consequat. Duis aute irure dolor in reprehenderit in voluptate velit esse cillum dolore eu fugiat nulla pariatur.</p>
      <p class="para">Lorem ipsum dolor sit amet, consectetur adipisicing elit, sed do eiusmod tempor incididunt ut labore et dolore magna aliqua. Ut enim ad minim veniam, quis nostrud exercitation ullamco laboris nisi ut aliquip ex ea commodo consequat.</p>
      <p class="para">Excepteur sint occaecat cupidatat non proident, sunt in culpa qui officia deserunt mollit anim id est laborum. re et dolore magnam aliquam quaerat voluptatem.</p>
      <p class="closing">Regards</p>
      <p class="signature">Daniel Brooks</p>
    </article>

    <div class="footer-rule" aria-hidden="true"></div>
    <div class="footer-band" aria-hidden="true"></div>
  </main>
</body>
</html>
```